Glen Whitmore Professional Coaching

I would like a website with a mountain theme geared towards professional executives reaching higher peaks and goals. This is a 3 page website with brand essence information on the opening page, the coaching process on a second page and "about me" and lead capture form on a third page

Target Market(s)

C-Level audience, involved in tech, government, manufacturing, and transportation type of corporations

Coding

Coded - Design and coding required

Number of Pages Required

3 page

Font styles to use
Sans Serif

Colors
a7a7a7
1b1b1b
e8e8e8
3176b5
abd036
0355a3

Requirements
Must have
• Looking for a user friendly site that I can manage/update going forward. Must have:
• 1. "Is coaching right for you?" - page 1
• 2. "Our Process" page 2 - I will describe how we approach coaching
• 3. "Contact us" page 3 where I can capture contact information from potential clients
• 4. Clean and professional with more modern font
• 5. Links to personal social media sites
• 6. Ability to upload/download .pdf documents as resources
• 7. Ability to add on new pages in the future (such as a blog page)
Nice to have
• I want a place to store articles I write or use.
• Linkwork or Chirp Feed
Should not have
• Not fluffy or too 'zen' like personal life coaches tend to present.

```html
<!DOCTYPE html>
<html lang="en">
<head>
<meta charset="utf-8">
<title>Glen Whitmore Professional Coaching</title>
<link href="https://fonts.googleapis.com/css2?family=PT+Sans:wght@400;700&family=PT+Serif&family=Roboto:wght@400;500&display=swap" rel="stylesheet">
<style>
:root{
  --ink:#1b1b1b;
  --text:#555555;
  --muted:#a7a7a7;
  --light:#e8e8e8;
  --blue:#3176b5;
  --blue-deep:#0355a3;
  --tint:#e3f0fa;
  --white:#ffffff;
  --black:#000000;
}
*{margin:0;padding:0;box-sizing:border-box}
html,body{width:1200px;height:3056px;overflow:hidden;background:var(--white)}
body{position:relative;font-family:"Roboto",sans-serif;color:var(--ink)}
.abs{position:absolute}

.hero{left:0;top:0;width:1200px;height:790px;
  background:linear-gradient(180deg,#4c4565 0%,#8a6a80 14%,#c9b4bf 24%,#a89aa8 40%,#7f7080 58%,#8c8090 72%,#d9d6dd 86%,#ffffff 100%)}
.nav{top:70px;left:0;width:1200px;display:flex;justify-content:center;gap:40px;font-size:19px;font-family:"Roboto",sans-serif}
.nav a{color:var(--white);text-decoration:none}
.nav a.active{color:var(--blue)}
.hero-title{top:342px;width:1200px;text-align:center;font-family:"PT Serif",serif;font-weight:400;font-size:42px;color:var(--white)}
.hero-sub{top:412px;width:1200px;text-align:center;font-family:"PT Sans",sans-serif;font-weight:700;font-size:26px;color:var(--white)}

.portrait{left:114px;top:878px;width:371px;height:377px;background:linear-gradient(160deg,#3e5a35,#6f8b54 45%,#2c3c5c 75%,#5a4a3a);border:2px solid var(--light)}
.section-title{font-family:"PT Sans",sans-serif;font-size:37px;color:var(--ink);font-weight:400}
.about-title{left:542px;top:880px}
.body-copy{font-size:13px;line-height:28px;color:var(--text)}
.about-p1{left:542px;top:938px;width:546px}
.about-p2{left:542px;top:1094px;width:546px}
.btn{display:flex;align-items:center;justify-content:center;border:2px solid #333;font-family:"Roboto",sans-serif;font-weight:500;font-size:15px;color:var(--ink);background:var(--white)}
.about-btn{left:542px;top:1204px;width:125px;height:42px}

.process-title{top:1400px;width:1200px;text-align:center}
.step-art{border-radius:40px;background:var(--tint)}
.step-title{font-family:"PT Sans",sans-serif;font-weight:400;font-size:26px;color:var(--blue)}
.step-copy{width:455px}

.cta{left:0;top:2250px;width:1200px;height:406px;background:linear-gradient(180deg,#ffffff 0%,#d4d4d6 22%,#eeeeee 40%,#f4f4f4 65%,#ffffff 100%)}
.cta-pre{top:2334px;width:1200px;text-align:center;font-family:"PT Sans",sans-serif;font-size:27px}
.cta-main{top:2360px;width:1200px;text-align:center;font-family:"PT Sans",sans-serif;font-size:86px;letter-spacing:2px}
.cta-btn{left:523px;top:2481px;width:154px;height:42px}

.footer{left:0;top:2656px;width:1200px;height:400px;background:var(--black);color:var(--white)}
.fcol{top:58px}
.fcol .rule{width:150px;height:1px;background:#777;margin-bottom:30px}
.fcol h3{font-family:"Roboto",sans-serif;font-weight:400;font-size:16px;margin-bottom:14px}
.fcol li{list-style:none;font-size:13.5px;height:31px}
.fcol li span.ic{display:inline-block;width:24px}
.social{top:283px;left:1010px;display:flex;gap:12px;font-size:12px;font-weight:500}
.divider{top:322px;left:110px;width:980px;height:1px;background:#555}
.copyright{top:354px;left:110px;font-size:12.5px}
.pay{top:352px;left:760px;display:flex;gap:16px;font-size:13px;font-weight:500;color:var(--blue)}
</style>
</head>
<body>

<header class="abs hero" role="img" aria-label="Snow-capped mountain peaks at dusk fading into white">
</header>
<nav class="abs nav">
  <a class="active" href="#">Home</a><a href="#">About</a><a href="#">Coaching Process</a>
</nav>
<h1 class="abs hero-title">Glen Whitmore Professional Coaching</h1>
<p class="abs hero-sub">Professional Executives</p>

<div class="abs portrait" role="img" aria-label="Portrait of the coach in a blazer outdoors"></div>
<h2 class="abs section-title about-title">ABOUT ME</h2>
<p class="abs body-copy about-p1">Sed ut perspiciatis unde omnis iste natus error sit voluptatem accusantium doloremque laud antium, totam rem aperiam, eaque ipsa quae ab illo inventore veritatis et quasi archit ecto beatae vitae dicta sunt explicabo. Nemo enim ipsam voluptatem quia voluptas sit asp ernatur aut odit aut fugit, sed quia consequuntur magni dolores eos qui ratione volupt atem sequi nesciu dolorem imagnam aliquam quaerat voluptatem.</p>
<p class="abs body-copy about-p2">Natus error sit voluptatem accusantium doloremque laudantium, totamem aperiam, eaque ipsa quae abillo inventore veritatis et quasi architecto beatae vitae dicta sunt explic abocons equuntur magni dolores eos .</p>
<a class="abs btn about-btn">READ MORE</a>

<h2 class="abs section-title process-title">COACHING PROCESS</h2>

<svg class="abs" style="left:0;top:1480px" width="1200" height="520" viewBox="0 0 1200 520">
  <path d="M450 110 C520 150 520 230 600 230 C680 230 730 225 770 250" fill="none" stroke="#3176b5" stroke-width="3" stroke-dasharray="2 7" stroke-linecap="round"/>
  <path d="M760 405 C700 430 520 430 410 485" fill="none" stroke="#3176b5" stroke-width="3" stroke-dasharray="2 7" stroke-linecap="round"/>
</svg>

<div class="abs step-art" style="left:193px;top:1497px;width:255px;height:173px" role="img" aria-label="Illustration of a monitor with a login screen"></div>
<h3 class="abs step-title" style="left:593px;top:1524px">1. Magnam aliquam quaerat</h3>
<p class="abs body-copy step-copy" style="left:593px;top:1566px">Natus error sit voluptatem accusantium doloremque laudantium, totamem aperiam, eaque ipsa quae abillo inventore veritatis et quasi architecto beatae vitae dicta sunt explic abocons equuntur magni dolores eos .</p>

<h3 class="abs step-title" style="left:161px;top:1754px">2.&nbsp; Dolorem eumuo voluptas</h3>
<p class="abs body-copy step-copy" style="left:161px;top:1794px">Natus error sit voluptatem accusantium doloremque laudantium, totamem aperiam, eaque ipsa quae abillo inventore veritatis et quasi architecto beatae vitae dicta sunt explic abocons equuntur magni dolores eos .</p>
<div class="abs step-art" style="left:709px;top:1721px;width:248px;height:173px" role="img" aria-label="Illustration of a document being signed with a pen"></div>

<div class="abs step-art" style="left:187px;top:1966px;width:257px;height:163px" role="img" aria-label="Illustration of a laptop with two people chatting"></div>
<h3 class="abs step-title" style="left:593px;top:1986px">3. Qui dolorem ipsum quia dolor</h3>
<p class="abs body-copy step-copy" style="left:593px;top:2028px">Natus error sit voluptatem accusantium doloremque laudantium, totamem aperiam, eaque ipsa quae abillo inventore veritatis et quasi architecto beatae vitae dicta sunt explic abocons equuntur magni dolores eos .</p>

<div class="abs cta" role="img" aria-label="Misty snowy mountain range in soft grey"></div>
<div class="abs" style="left:599px;top:2184px;width:1px;height:128px;background:#cfcfcf"></div>
<p class="abs cta-pre">Want to see</p>
<p class="abs cta-main">MORE ?</p>
<a class="abs btn cta-btn">READ MORE</a>

<footer class="abs footer">
  <div class="abs fcol" style="left:110px">
    <div class="rule"></div><h3>QUICK LINKS</h3>
    <ul><li>Home</li><li>About Me</li><li>Coaching Process</li><li>Contact</li></ul>
  </div>
  <div class="abs fcol" style="left:358px">
    <div class="rule"></div><h3>GET IN TOUCH</h3>
    <ul><li>Ask Question</li></ul>
  </div>
  <div class="abs fcol" style="left:615px">
    <div class="rule"></div><h3>CONTACT US</h3>
    <ul>
      <li><span class="ic"><svg width="12" height="12" viewBox="0 0 24 24"><path fill="#fff" d="M6.6 10.8a15 15 0 0 0 6.6 6.6l2.2-2.2c.3-.3.7-.4 1-.2 1.1.4 2.3.6 3.6.6.6 0 1 .4 1 1V20c0 .6-.4 1-1 1A17 17 0 0 1 3 4c0-.6.4-1 1-1h3.5c.6 0 1 .4 1 1 0 1.3.2 2.5.6 3.6.1.3 0 .7-.2 1z"/></svg></span>(+1) 555 010 0199</li>
      <li><span class="ic"><svg width="12" height="10" viewBox="0 0 24 18"><path fill="#fff" d="M0 0h24v2L12 10 0 2zM0 4l12 8 12-8v14H0z"/></svg></span>support@glenwhitmore.com</li>
      <li><span class="ic"><svg width="10" height="13" viewBox="0 0 20 26"><path fill="#fff" d="M10 0a10 10 0 0 0-10 10c0 7 10 16 10 16s10-9 10-16A10 10 0 0 0 10 0zm0 14a4 4 0 1 1 0-8 4 4 0 0 1 0 8z"/></svg></span>Lorem Ipsum Is Simply Dummy,</li>
      <li><span class="ic"></span>Lorem Ipsum.</li>
    </ul>
  </div>
  <div class="abs social"><span>Facet</span><span>Chirp</span><span>Linkwork</span></div>
  <div class="abs divider"></div>
  <p class="abs copyright">Copyright © 2019. All Rights Reserved.</p>
  <div class="abs pay"><span>Ferncard</span><span>Tallowpay</span><span>Ostrel</span><span>Kestwire</span><span>Brindlenet</span></div>
</footer>

</body>
</html>
```